Design Project - Finance Website (Only need PSD)

UPDATED PROJECT (Now only PSD needed)
Need a Wordpress design for a company called "Corvale Lending Partners". The company provides finance for corporate clients, businesses and property developers. The design should be business like with appealing colours that communicate trust. I have uploaded a banner and logo to be incorporated or feel free to design something better if you think you can.
** I now only need the PSD
** I want something that is actually designed rather than from a template.
Thanks
Updates
The website will be used for lead generation so the contact form with adjustable fields in the Wordpress backend should be fairly prominent on the page.
I have uploaded a banner and logo for the site. None of the designs I have seen so far were good enough so the first decent design using the new banner and logo provided will win the job. I do not want just a template that has been cut and paste from somewhere else, I want decent design. If anyone provides a decent design then I will give an extra bonus of $150.
Reason: I have uploaded a banner and logo for the site. None of the designs I have seen so far were good enough so the first decent design using the new banner and logo provided will win the job. I do not want just a template that has been cut and paste from somewhere else, I want decent design. If anyone provides a decent design then I will give an extra bonus of $150.
Thanks
Target Market(s)
Business owners & property developers
Industry/Entity Type
Finance
Requirements
Must have
- Contact form on home page that can be altered through the back end eg. ability to add or remove fields. Widgetised sidebars.
Nice to have
- Widgetised footer.

```html
<!DOCTYPE html>
<html lang="en">
<head>
<meta charset="utf-8">
<title>Corvale Lending Partners</title>
<link href="https://fonts.googleapis.com/css2?family=Open+Sans:wght@400;600&family=Arimo:wght@400&display=swap" rel="stylesheet">
<style>
:root{
  --sky-top:#2f6db0;
  --sky-bottom:#5fb8e0;
  --nav-dark:#2b2b2b;
  --nav-line:#555;
  --green:#6cb33f;
  --page-grey:#e6e8ea;
  --panel:#ffffff;
  --ink:#333;
  --soft:#8a8a8a;
  --accent-red:#c00000;
  --footer:#eeeeee;
  --dot-blue:#2d5ea8;
}
*{box-sizing:border-box;margin:0;padding:0}
html,body{width:915px;height:1200px;overflow:hidden;background:#fff}
body{font-family:"Arimo",Arial,sans-serif;color:var(--ink);position:relative}
.abs{position:absolute}
.site-header{left:0;top:0;width:915px;height:104px;background:linear-gradient(180deg,var(--sky-top),var(--sky-bottom))}
.brand{left:38px;top:18px;font-family:"Open Sans",sans-serif;font-size:31px;color:#fff;letter-spacing:.2px}
.search{left:600px;top:14px;width:185px;height:24px;border-radius:5px;background:linear-gradient(#fff,#ddd);border:1px solid #555;font-size:12px;color:#444;padding:4px 10px}
.search svg{position:absolute;right:8px;top:4px}
.social-top{top:14px;width:24px;height:24px;border-radius:3px;background:#1f5f99;border:1px solid #7fb0d8}
.nav{left:396px;top:51px;width:510px;height:36px;display:flex;background:linear-gradient(#3b3b3b,#1e1e1e);border-radius:3px;font-family:"Open Sans",sans-serif;font-size:12px}
.nav a{color:#eee;text-decoration:none;display:flex;align-items:center;justify-content:center;border-right:1px solid var(--nav-line)}
.nav a.current{background:var(--green);color:#fff}
.hero-band{left:0;top:104px;width:915px;height:303px;background:var(--page-grey)}
.hero{left:24px;top:119px;width:867px;height:265px;border-radius:5px;background:linear-gradient(160deg,#6a9fc0 0%,#3e7e9e 40%,#2b5a70 70%,#1d3a4a 100%);box-shadow:0 8px 10px -6px rgba(0,0,0,.5)}
.hero-points{left:540px;top:265px;font-family:"Open Sans",sans-serif;font-style:italic;font-size:18px;color:#fff;line-height:38px;text-shadow:1px 1px 2px rgba(0,0,0,.6)}
.dots{left:383px;top:392px;display:flex;gap:4px}
.dots span{width:9px;height:9px;border-radius:50%;background:#111}
.dots span:first-child{background:var(--dot-blue)}
.grey-mid{left:0;top:407px;width:915px;height:316px;background:var(--page-grey)}
.welcome{left:23px;top:431px;width:870px;height:266px;background:var(--panel);border-radius:8px}
.welcome h1{position:absolute;left:20px;top:10px;font-family:"Open Sans",sans-serif;font-weight:400;font-size:18px;color:#333}
.welcome-rule{left:0;top:38px;width:870px;height:8px;background:linear-gradient(#f2f2f2,#fff)}
.welcome-photo{left:44px;top:492px;width:267px;height:178px;background:linear-gradient(135deg,#e9dcc6,#b9a37e 55%,#7a2a22);border:4px solid #fff;box-shadow:0 0 3px rgba(0,0,0,.35)}
.welcome-copy{left:328px;top:494px;width:540px;font-size:11.8px;line-height:16.5px;color:#444}
.welcome-copy p+p{margin-top:16px}
.btn{border-radius:10px;background:linear-gradient(#fff,#eee);box-shadow:0 1px 3px rgba(0,0,0,.35);color:var(--accent-red);font-size:12.5px;display:flex;align-items:center;justify-content:center}
.section-title{font-family:"Open Sans",sans-serif;font-size:16px;color:#222}
.news-thumb{left:11px;width:86px;height:60px;border:1px solid #7a8fa8;background:linear-gradient(135deg,#dfe9f5,#2f5fa8)}
.small{font-size:10px;line-height:16.5px;color:var(--soft)}
.case-icon{left:329px;top:796px;width:101px;height:61px;background:linear-gradient(135deg,#f6c64b,#d98b1d);border-radius:6px}
.field{left:679px;width:206px;height:24px;border:1px solid #ccc;background:#f7f7f7;font-size:10px;color:#666;padding:5px 16px}
.footer{left:0;top:1046px;width:915px;height:127px;background:repeating-linear-gradient(135deg,#ececec 0 3px,#f6f6f6 3px 6px);border-top:2px solid #ddd}
.footer-base{left:0;top:1173px;width:915px;height:27px;background:#f4f4f4}
.foot-col{top:1072px;font-size:12px;line-height:19.2px;color:#333;list-style:none}
.foot-col li::before{content:"›";margin-right:7px;font-weight:bold;color:#555}
.foot-brand{left:651px;top:1080px;font-family:"Open Sans",sans-serif;font-size:15px;color:#999}
.foot-icon{top:1112px;width:21px;height:21px;border-radius:2px}
.copy{right:19px;top:1150px;font-size:10px;color:#333}
</style>
</head>
<body>
<header class="abs site-header">
  <div class="abs brand">Corvale Lending Partners</div>
  <div class="abs search">search
    <svg width="12" height="12" viewBox="0 0 12 12"><circle cx="5" cy="5" r="3.5" fill="none" stroke="#444" stroke-width="1.5"/><line x1="7.5" y1="7.5" x2="11" y2="11" stroke="#444" stroke-width="1.8"/></svg>
  </div>
  <div class="abs social-top" style="left:808px" aria-label="Social profile"></div>
  <div class="abs social-top" style="left:843px" aria-label="Social profile"></div>
  <div class="abs social-top" style="left:878px" aria-label="Social profile"></div>
  <nav class="abs nav">
    <a class="current" style="width:60px">Home</a>
    <a style="width:96px">About Us</a>
    <a style="width:84px">Services</a>
    <a style="width:84px">Finance</a>
    <a style="width:92px">Real Estate</a>
    <a style="width:94px;border-right:0">Contact Us</a>
  </nav>
</header>

<div class="abs hero-band"></div>
<div class="abs hero" role="img" aria-label="Glass office building photographed from below against a blue sky"></div>
<div class="abs hero-points">
  <div>→ Compare several capital provider rates</div>
  <div>→ Access to real estate and hedge funds</div>
  <div>→ Optimise your capital returns</div>
</div>
<div class="abs dots"><span></span><span></span><span></span><span></span><span></span></div>

<div class="abs grey-mid"></div>
<section class="abs welcome">
  <div class="abs welcome-rule"></div>
  <h1>Welcome to Corvale Lending Partners</h1>
</section>
<div class="abs welcome-photo" role="img" aria-label="Bright living room interior with red sofas"></div>
<div class="abs welcome-copy">
  <p>Lorem ipsum dolor sit amet, tollite fit omnibus civitas ad quia. Quaere ait regem ut .Lorem ipsum dolor sit amet, tollite fit omnibus civitas ad quia. Quaere ait regem ut .Lorem ipsum dolor sit amet, tollite fit omnibus civitas ad quia. Quaere ait regem ut .Lorem ipsum dolor sit amet, tollite fit omnibus civitas ad quia. Quaere ait regem ut .</p>
  <p>Lorem ipsum dolor sit amet, tollite fit omnibus civitas ad quia. Quaere ait regem ut .Lorem ipsum dolor sit amet, tollite fit omnibus civitas ad quia. Quaere ait regem ut .Lorem ipsum dolor sit amet, tollite fit omnibus civitas ad quia. Quaere ait regem ut .Lorem ipsum dolor sit amet, tollite fit omnibus civitas ad quia. Quaere ait regem ut .</p>
</div>
<div class="abs btn" style="left:731px;top:643px;width:135px;height:36px">READ MORE</div>

<h2 class="abs section-title" style="left:13px;top:752px">LATEST NEWS</h2>
<div class="abs news-thumb" style="top:793px" role="img" aria-label="Business news illustration"></div>
<div class="abs news-thumb" style="top:878px;background:linear-gradient(135deg,#3a6fc8,#0c1f55)" role="img" aria-label="Business team silhouettes"></div>
<div class="abs news-thumb" style="top:961px;background:linear-gradient(180deg,#6fa8e0,#cfe3f4 60%,#7cbf3a)" role="img" aria-label="Puzzle pieces over a green field"></div>
<p class="abs small" style="left:109px;top:791px;width:185px">Nunc varius facilisis eros. Sed erat. In in velit quis arcu ornare laoreet. Curabitur adipiscing luctus massa.Integer ut purus ac augue commodo .</p>
<p class="abs small" style="left:109px;top:877px;width:185px">Nunc varius facilisis eros. Sed erat. In in velit quis arcu ornare laoreet. Curabitur adipiscing luctus massa.Integer ut purus ac augue commodo .</p>
<p class="abs small" style="left:109px;top:958px;width:185px">Nunc varius facilisis eros. Sed erat. In in velit quis arcu ornare laoreet. Curabitur adipiscing luctus massa.Integer ut purus ac augue commodo .</p>

<h2 class="abs section-title" style="left:328px;top:749px">CASE STUDY</h2>
<div class="abs case-icon" role="img" aria-label="Folders with a magnifying glass"></div>
<p class="abs small" style="left:438px;top:799px;width:178px">Nunc varius facilisis eros. Sed erat. In in velit quis arcu ornare laoreet. Curabitur adipiscing luctus massa. Integer ut purus ac augue commodo .</p>
<p class="abs small" style="left:341px;top:878px;width:280px">Nunc varius facilisis eros. Sed erat. In in velit quis arcu ornare laoreet. Curabitur adipiscing luctus massa.Integer ut purus ac augue commodo . Nunc varius facilisis eros. Sed erat. In in velit quis arcu ornare laoreet. Curabitur adipiscing luctus massa.Integer ut purus ac augue commodo .</p>
<div class="abs" style="left:343px;top:971px;font-size:12.5px;color:var(--accent-red)">READ MORE</div>

<h2 class="abs section-title" style="left:667px;top:749px">QUICK CONTACT</h2>
<div class="abs field" style="top:788px">Name</div>
<div class="abs field" style="top:825px">Email Address</div>
<div class="abs field" style="top:863px">Phone</div>
<div class="abs" style="left:679px;top:901px;width:16px;height:16px;border:1px solid #ccc;background:#f7f7f7"></div>
<div class="abs" style="left:706px;top:903px;font-size:10px;color:#666">Subscribe to Our Newsletter</div>
<div class="abs btn" style="left:679px;top:934px;width:90px;height:33px">SUBMIT</div>

<footer class="abs footer"></footer>
<ul class="abs foot-col" style="left:44px"><li>About Us</li><li>Contact Us</li><li>Services</li><li>Loreum ipsum</li><li>Other links</li></ul>
<ul class="abs foot-col" style="left:219px"><li>About Us</li><li>Contact Us</li><li>Services</li><li>Loreum ipsum</li><li>Other links</li></ul>
<ul class="abs foot-col" style="left:375px"><li>About Us</li><li>Contact Us</li><li>Services</li><li>Loreum ipsum</li><li>Other links</li></ul>
<div class="abs foot-brand">Corvale Lending Partners</div>
<div class="abs foot-icon" style="left:653px;background:#3b5a9a"></div>
<div class="abs foot-icon" style="left:690px;background:#5fb0e0"></div>
<div class="abs foot-icon" style="left:727px;background:#e8731d"></div>
<div class="abs foot-icon" style="left:763px;background:#1c6fa6"></div>
<div class="abs foot-icon" style="left:800px;background:#4a8f3c"></div>
<div class="abs copy">© 2012 Corvale Lending Partners, All Rights Reserved</div>
<div class="abs footer-base"></div>
</body>
</html>
```